Business Card Design

Company is a Commercial Building Company specialising in New Construction and existing refurbishments

Industry/Entity Type

Business

Contact Information for Business Card

Liam Porter
Construction Manager
E Liam@marshbuilding.com.au
M 0400 213 594
Mail 14 Tarrant Rise Harbourvale WA 6219

```html
<!DOCTYPE html>
<html lang="en">
<head>
<meta charset="utf-8">
<title>Marsh Building &amp; Construction — Business Card</title>
<link href="https://fonts.googleapis.com/css2?family=Barlow+Condensed:wght@400;600&family=Barlow:wght@400;500&display=swap" rel="stylesheet">
<style>
  :root {
    --teal: #15bdd9;
    --teal-deep: #0fb0cc;
    --navy: #2e3945;
    --white: #ffffff;
    --paper: #eeeeec;
    --faint: rgba(255, 255, 255, 0.28);
  }
  * { box-sizing: border-box; margin: 0; padding: 0; }
  html, body {
    width: 1200px;
    height: 857px;
    overflow: hidden;
    background: var(--paper);
  }
  .stage {
    width: 1200px;
    height: 857px;
    display: flex;
    align-items: center;
    justify-content: center;
    gap: 60px;
  }
  .card {
    position: relative;
    width: 500px;
    height: 304px;
    border-radius: 26px;
    overflow: hidden;
    box-shadow: 0 2px 8px rgba(0, 0, 0, 0.12);
  }

  /* Front */
  .card--front { background: var(--white); }
  .brand {
    position: absolute;
    top: 78px;
    left: 150px;
    display: flex;
    align-items: center;
    gap: 14px;
  }
  .brand__square {
    width: 40px;
    height: 40px;
    background: var(--teal);
  }
  .brand__name {
    font-family: "Barlow Condensed", sans-serif;
    font-weight: 600;
    color: var(--navy);
    text-transform: uppercase;
    line-height: 0.95;
  }
  .brand__main { display: block; font-size: 34px; letter-spacing: 0.5px; }
  .brand__sub { display: block; font-size: 22px; letter-spacing: 1px; }
  .front-band {
    position: absolute;
    left: 0; right: 0; bottom: 0;
    height: 66px;
    background: var(--teal);
    display: flex;
    flex-direction: column;
    align-items: center;
    justify-content: center;
    gap: 2px;
  }
  .person__name {
    font-family: "Barlow Condensed", sans-serif;
    font-weight: 600;
    font-size: 22px;
    color: var(--white);
    text-transform: uppercase;
    letter-spacing: 0.5px;
  }
  .person__role {
    font-family: "Barlow Condensed", sans-serif;
    font-weight: 400;
    font-size: 14px;
    color: var(--white);
    text-transform: uppercase;
    letter-spacing: 1px;
  }

  /* Back */
  .card--back { background: linear-gradient(160deg, var(--teal) 0%, var(--teal-deep) 100%); }
  .back-brand {
    position: absolute;
    top: 40px;
    right: 34px;
    font-family: "Barlow Condensed", sans-serif;
    font-weight: 600;
    color: var(--faint);
    text-transform: uppercase;
    line-height: 0.95;
    text-align: left;
  }
  .back-brand__main { display: block; font-size: 30px; }
  .back-brand__sub { display: block; font-size: 19px; letter-spacing: 1px; }
  .contact-list {
    position: absolute;
    left: 40px;
    bottom: 40px;
    width: 250px;
    list-style: none;
  }
  .contact-item {
    display: flex;
    align-items: center;
    gap: 10px;
    padding: 9px 0;
    border-top: 1px solid rgba(255, 255, 255, 0.55);
    font-family: "Barlow", sans-serif;
    font-weight: 500;
    font-size: 14px;
    color: var(--white);
    line-height: 1.25;
  }
  .contact-item:first-child { border-top: none; }
  .contact-icon { flex: 0 0 16px; width: 16px; height: 16px; }
</style>
</head>
<body>
<main class="stage">

  <section class="card card--front" aria-label="Business card front">
    <div class="brand">
      <span class="brand__square"></span>
      <p class="brand__name">
        <span class="brand__main">Marsh Building</span>
        <span class="brand__sub">&amp; Construction</span>
      </p>
    </div>
    <div class="front-band">
      <p class="person__name">Liam Porter</p>
      <p class="person__role">Construction Manager</p>
    </div>
  </section>

  <section class="card card--back" aria-label="Business card back">
    <p class="back-brand">
      <span class="back-brand__main">Marsh Building</span>
      <span class="back-brand__sub">&amp; Construction</span>
    </p>
    <ul class="contact-list">
      <li class="contact-item">
        <svg class="contact-icon" viewBox="0 0 16 16" aria-hidden="true">
          <circle cx="8" cy="8" r="8" fill="#fff"/>
          <rect x="4" y="5" width="8" height="6" fill="none" stroke="#15bdd9" stroke-width="1.2"/>
          <path d="M4 5 L8 8.5 L12 5" fill="none" stroke="#15bdd9" stroke-width="1.2"/>
        </svg>
        Liam@marshbuilding.com.au
      </li>
      <li class="contact-item">
        <svg class="contact-icon" viewBox="0 0 16 16" aria-hidden="true">
          <circle cx="8" cy="8" r="8" fill="#fff"/>
          <rect x="5.5" y="3.5" width="5" height="9" rx="1" fill="none" stroke="#15bdd9" stroke-width="1.2"/>
          <circle cx="8" cy="11" r="0.7" fill="#15bdd9"/>
        </svg>
        0400 213 594
      </li>
      <li class="contact-item">
        <svg class="contact-icon" viewBox="0 0 16 16" aria-hidden="true">
          <circle cx="8" cy="8" r="8" fill="#fff"/>
          <path d="M8 3.5 C5.8 3.5 4.8 5 4.8 6.5 C4.8 8.6 8 12.5 8 12.5 C8 12.5 11.2 8.6 11.2 6.5 C11.2 5 10.2 3.5 8 3.5 Z" fill="#15bdd9"/>
          <circle cx="8" cy="6.5" r="1.2" fill="#fff"/>
        </svg>
        <span>14 Tarrant Rise<br>Harbourvale WA 6219</span>
      </li>
    </ul>
  </section>

</main>
</body>
</html>
```